Puffy Clouds Cotton Candy

Looking for a logo design and business cards to help a 13 year old entrepreneur promote her cotton candy business.
Contact Information for Business Card
Name, Phone & Email
Colors
E54698
E96AAD
F1A4CE
F9D9EA
FCEFF6
A7469A
B969AE
D3A5CF
EDDBEB
F8F0F9
6B429C
8869AF
B7A5CE
E3DAEB
F3F0F8
Requirements
Must have
- A fun feel that is appropriate for a teenage girl selling cotton candy

```html
<!DOCTYPE html>
<html lang="en">
<head>
<meta charset="utf-8">
<title>Puffy Clouds Cotton Candy – Business Cards</title>
<link rel="stylesheet" href="https://fonts.googleapis.com/css2?family=Jost:wght@400;500;600&family=Arimo:wght@400&display=swap">
<style>
  :root {
    --backdrop: #444444;
    --pink: #E54698;
    --purple: #6B429C;
    --white: #ffffff;
    --shadow: rgba(0, 0, 0, 0.55);
  }
  * { margin: 0; padding: 0; box-sizing: border-box; }
  html, body {
    width: 1075px;
    height: 1200px;
    overflow: hidden;
    background: var(--backdrop);
  }
  .canvas { position: relative; width: 1075px; height: 1200px; }

  .card {
    position: absolute;
    left: 206px;
    width: 663px;
    height: 395px;
    overflow: hidden;
    box-shadow: 3px 3px 2px var(--shadow);
  }
  .card--front { top: 187px; background: var(--white); }
  .card--back { top: 637px; background: var(--pink); }

  .front__band {
    position: absolute;
    left: 0; right: 0;
    top: 234px; bottom: 0;
    background: var(--pink);
    border-top: 6px solid var(--purple);
  }

  .brand-ring { position: absolute; }
  .brand-name {
    position: absolute;
    font-family: "Jost", sans-serif;
    font-weight: 500;
    line-height: 1;
    white-space: nowrap;
  }
  .front .brand-name { color: var(--pink); }

  .front__name-line1 { left: 302px; top: 88px; font-size: 42px; }
  .front__name-line2 { left: 303px; top: 131px; font-size: 26px; }

  .back__name-line1, .back__name-line2 {
    left: 0; right: 0; text-align: center; color: var(--white);
  }
  .back__name-line1 { top: 249px; font-size: 54px; }
  .back__name-line2 { top: 296px; font-size: 33px; }

  .holder {
    position: absolute;
    right: calc(663px - 314px);
    text-align: right;
    color: var(--white);
    line-height: 1;
    white-space: nowrap;
  }
  .holder__name {
    top: 298px;
    font-family: "Jost", sans-serif;
    font-weight: 600;
    font-size: 25px;
  }
  .holder__title {
    top: 322px;
    font-family: "Arimo", sans-serif;
    font-size: 17px;
  }
  .divider {
    position: absolute;
    left: 332px; top: 303px;
    width: 1.5px; height: 42px;
    background: var(--white);
  }
  .contact {
    position: absolute;
    left: 353px;
    display: flex;
    align-items: center;
    gap: 5px;
    color: var(--white);
    font-family: "Arimo", sans-serif;
    font-size: 17px;
    line-height: 1;
    white-space: nowrap;
  }
  .contact--phone { top: 301px; }
  .contact--email { top: 325px; }
  .contact__icon { width: 18px; height: 16px; flex: none; }
</style>
</head>
<body>
<main class="canvas">

  <section class="card card--front front">
    <svg class="brand-ring" style="left:152px;top:54px" width="130" height="130" viewBox="0 0 130 130" aria-hidden="true">
      <circle cx="65" cy="65" r="61" fill="none" stroke="var(--pink)" stroke-width="5"/>
    </svg>
    <div class="brand-name front__name-line1">Puffy Clouds</div>
    <div class="brand-name front__name-line2">Cotton Candy</div>

    <div class="front__band"></div>

    <div class="holder holder__name">Madison Clarke</div>
    <div class="holder holder__title">Managing Director</div>
    <div class="divider"></div>

    <div class="contact contact--phone">
      <svg class="contact__icon" viewBox="0 0 18 16" aria-hidden="true">
        <path d="M4 1.5c.8-.4 1.5 0 1.9.8l1 2c.3.7.1 1.3-.5 1.7l-.9.6c.6 1.5 1.8 2.9 3.3 3.6l.7-.8c.5-.5 1.1-.6 1.7-.2l1.9 1.2c.7.5.9 1.2.4 1.9-1 1.4-2.3 2-3.9 1.4C6 12.5 3.3 9.6 2.5 6.3 2.1 4.4 2.6 2.4 4 1.5z" fill="var(--white)"/>
        <path d="M11 2.5a4.5 4.5 0 0 1 4 4M11 5a2 2 0 0 1 1.7 1.7" fill="none" stroke="var(--white)" stroke-width="1.3" stroke-linecap="round"/>
      </svg>
      <span>044-555 012 347</span>
    </div>
    <div class="contact contact--email">
      <svg class="contact__icon" viewBox="0 0 18 16" aria-hidden="true">
        <rect x="1" y="3" width="16" height="10" fill="var(--white)"/>
        <path d="M1 3l8 6 8-6M1 13l6-5M17 13l-6-5" fill="none" stroke="var(--pink)" stroke-width="1.2"/>
      </svg>
      <span>hello@sitename.com</span>
    </div>
  </section>

  <section class="card card--back back">
    <svg class="brand-ring" style="left:251px;top:61px" width="162" height="162" viewBox="0 0 162 162" aria-hidden="true">
      <circle cx="81" cy="81" r="76" fill="none" stroke="var(--white)" stroke-width="6"/>
    </svg>
    <div class="brand-name back__name-line1">Puffy Clouds</div>
    <div class="brand-name back__name-line2">Cotton Candy</div>
  </section>

</main>
</body>
</html>
```